New Fun, Positive, energised looking Business Card Needed for High Achiever Coach

I am looking for a two sided full colour business card. I am self employed and have recently re branded my 1-2-1 work re-vitalising high achievers. My target client base for these cards is therefore high achievers - usually aged 40 -55, they are often entrepreneurs, CEO or work in banking and finance and 2/3 are male. I work with them on 90 day or 6 month coaching programs to help them live their success in a healthier, more sustainable and fulfiiled way. They pay for this privately so though they are corporate types the cards need not look 'corporate'. I want to portray the idea of transformation, vitality and re-connecting.
You can get a feel for the look I like on my new website: morvenlisk.co.uk
I want to use this logo with strapline (Re-Vitalising High Achievers) (I purchased off Logoharbor) and font/ colours (the turquoise and green).
Details to include on the card:
www.morvenlisk.co.uk
+44 7915 302618
morven@morvenlisk.co.uk
skype: morvenlisk
I'd also like to include:
Do you struggle to switch off? Want to be healthier and feel fitter? Want closer relationships? More clarity over the direction you are headed? I can help you do these things using integrated mind-body techniques. Visit morvenlisk.co.uk TODAY to apply for a FREE Breakthrough session.
BUT if that is too much text for a card I am open to advice/ammendments.
Updates
Thanks for your design - I am considering them. PLease change the wording to :

```html
<!DOCTYPE html>
<html lang="en">
<head>
<meta charset="utf-8">
<title>Morven Lisk – Business Card</title>
<link rel="stylesheet" href="https://fonts.googleapis.com/css2?family=PT+Sans:ital,wght@0,400;0,700;1,400&display=swap">
<style>
  :root {
    --ink: #000000;
    --turquoise: #00a6c9;
    --green: #5cbf6a;
    --white: #ffffff;
    --divider: #7a7a7a;
    --page: #e9e9ec;
  }
  * { box-sizing: border-box; margin: 0; padding: 0; }
  html, body { width: 1200px; height: 987px; overflow: hidden; }
  body {
    background: var(--page);
    font-family: "PT Sans", Arial, sans-serif;
    display: flex;
    flex-direction: column;
    align-items: center;
    justify-content: center;
    gap: 40px;
  }
  .card {
    position: relative;
    width: 760px;
    height: 434px;
    background: var(--ink);
    border-radius: 32px;
    overflow: hidden;
    color: var(--white);
  }

  /* Back side */
  .card-back .pitch {
    position: absolute;
    left: 44px;
    top: 110px;
    width: 680px;
    font-size: 19px;
    line-height: 25px;
  }
  .card-back .pitch p { white-space: nowrap; }
  .card-back .pitch .link { color: var(--green); font-weight: 700; }
  .card-back .brand-mark {
    position: absolute;
    right: 44px;
    top: 140px;
    display: flex;
    align-items: center;
    gap: 12px;
    color: var(--green);
    font-weight: 700;
    font-size: 36px;
    line-height: 1;
  }
  .brand-mark .dot {
    width: 20px; height: 20px; border-radius: 50%; background: var(--green);
  }

  /* Front side */
  .card-front .accent-band {
    position: absolute;
    left: 0;
    right: 0;
    bottom: 0;
    height: 96px;
    background: linear-gradient(90deg, var(--turquoise) 0%, var(--turquoise) 65%, var(--green) 100%);
  }
  .card-front .identity {
    position: absolute;
    left: 60px;
    top: 120px;
    width: 320px;
  }
  .identity .name {
    color: var(--turquoise);
    font-weight: 700;
    font-size: 48px;
    line-height: 1;
    white-space: nowrap;
  }
  .identity .strapline {
    margin-top: 10px;
    color: var(--turquoise);
    font-style: italic;
    font-size: 21px;
    white-space: nowrap;
  }
  .card-front .divider {
    position: absolute;
    left: 405px;
    top: 62px;
    width: 2px;
    height: 200px;
    background: linear-gradient(var(--ink), var(--divider), var(--ink));
  }
  .card-front .contacts {
    position: absolute;
    left: 436px;
    top: 84px;
    list-style: none;
    font-size: 22px;
  }
  .contacts li {
    display: flex;
    align-items: center;
    gap: 12px;
    height: 34px;
    white-space: nowrap;
  }
  .contacts svg { width: 18px; height: 18px; flex: none; }
</style>
</head>
<body>

<section class="card card-back" aria-label="Business card, back">
  <div class="pitch">
    <p>Do you struggle to switch off?</p>
    <p>Want to be healthier and feel fitter?</p>
    <p>Want closer relationships?</p>
    <p>More clarity over the direction you are headed?</p>
    <p>I can help you do these things using integrated mind-body techniques.</p>
    <p>Visit <span class="link">morvenlisk.co.uk</span> TODAY to apply for a FREE Breakthrough session.</p>
  </div>
  <div class="brand-mark"><span class="dot"></span>Morven Lisk</div>
</section>

<section class="card card-front" aria-label="Business card, front">
  <div class="accent-band" role="img" aria-label="Decorative turquoise and green accent area"></div>

  <div class="identity">
    <div class="name">Morven Lisk</div>
    <div class="strapline">Re-Vitalising High Achievers</div>
  </div>

  <div class="divider"></div>

  <ul class="contacts">
    <li>
      <svg viewBox="0 0 20 20" aria-hidden="true"><circle cx="10" cy="10" r="9" fill="none" stroke="var(--green)" stroke-width="2"/><path d="M7 5 L9 8 L8 9 C9 11 10 12 11 12 L12 11 L15 13 L13.5 15 C9 15 5 11 5 6.5 Z" fill="var(--green)"/></svg>
      +44 7915 302618
    </li>
    <li>
      <svg viewBox="0 0 20 20" aria-hidden="true"><rect x="2" y="5" width="16" height="11" rx="1" fill="var(--green)"/><path d="M2 6 L10 12 L18 6" fill="none" stroke="var(--ink)" stroke-width="1.5"/></svg>
      morven@morvenlisk.co.uk
    </li>
    <li>
      <svg viewBox="0 0 20 20" aria-hidden="true"><circle cx="10" cy="10" r="8" fill="none" stroke="var(--green)" stroke-width="2"/><ellipse cx="10" cy="10" rx="3.5" ry="8" fill="none" stroke="var(--green)" stroke-width="1.5"/><path d="M2 10 H18" stroke="var(--green)" stroke-width="1.5"/></svg>
      www.morvenlisk.co.uk
    </li>
    <li>
      <svg viewBox="0 0 20 20" aria-hidden="true"><circle cx="10" cy="10" r="8" fill="var(--turquoise)"/></svg>
      morvenlisk
    </li>
  </ul>
</section>

</body>
</html>
```